Velvette by Marisa Dunn business cards

I am after a business card that will fit the name of my business - velvette.
I want something classy and sexy and nothing tacky.
Ideas that I like are Zebra print backgrounds glitter back grounds
Two ideas I had were
1. Zebra print in black and white, the name Velvette by Marisa Dunn and a shilouette of a woman laying on top of the name. Or instead of zebra a glitter background.
2. Idea very similar except for instead of a woman a pair of lips maybe a hot pink glitter or a gold glitter depending on background with the business name between the lips.
Or you can do something completely different.

```html
<!DOCTYPE html>
<html lang="en">
<head>
<meta charset="utf-8">
<title>Velvette by Marisa Dunn – Business Card</title>
<link rel="stylesheet" href="https://fonts.googleapis.com/css2?family=Poppins:wght@700&family=Questrial&display=swap">
<style>
  :root {
    --paper: #ffffff;
    --ink-strong: #1c1a1a;
    --ink: #3d3d3d;
    --icon: #8a8a8a;
    --rule: #bdbdbd;
    --stripe-light: #ffffff;
    --stripe-tone: #e9e9e9;
  }
  * { margin: 0; padding: 0; box-sizing: border-box; }
  html, body {
    width: 1200px;
    height: 686px;
    overflow: hidden;
    background: var(--paper);
  }
  .card {
    position: relative;
    width: 1200px;
    height: 686px;
    background: var(--paper);
    font-family: "Questrial", "Century Gothic", sans-serif;
    color: var(--ink);
    overflow: hidden;
  }
  .card__pattern {
    position: absolute;
    left: 0;
    top: 187px;
    width: 1200px;
    height: 499px;
    background:
      linear-gradient(115deg, var(--stripe-tone) 0%, var(--stripe-light) 22%, var(--stripe-tone) 45%, var(--stripe-light) 65%, var(--stripe-tone) 85%, var(--stripe-light) 100%);
  }
  .card__header {
    position: absolute;
    left: 0;
    top: 0;
    width: 1200px;
    text-align: center;
  }
  .card__name {
    position: absolute;
    left: 0;
    top: 36px;
    width: 100%;
    font-family: "Poppins", "Century Gothic", sans-serif;
    font-weight: 700;
    font-size: 62px;
    line-height: 1;
    letter-spacing: 0.5px;
    color: var(--ink-strong);
  }
  .card__title {
    position: absolute;
    left: 0;
    top: 100px;
    width: 100%;
    font-size: 54px;
    line-height: 1;
    color: var(--ink);
  }
  .card__rule {
    position: absolute;
    left: 0;
    top: 179px;
    width: 905px;
    height: 8px;
    background: linear-gradient(90deg, var(--rule) 0%, var(--rule) 60%, rgba(189,189,189,0) 100%);
  }
  .contact {
    position: absolute;
    left: 0;
    width: 1200px;
    text-align: center;
    font-size: 47px;
    line-height: 62px;
    color: var(--ink);
  }
  .contact--address { top: 228px; }
  .contact--phone   { top: 394px; }
  .contact--mobile  { top: 487px; }
  .contact--email   { top: 580px; }
  .icon {
    position: absolute;
    fill: none;
    stroke: var(--icon);
    stroke-width: 2.2;
    stroke-linejoin: round;
    stroke-linecap: round;
  }
  .icon--home   { left: 126px; top: 214px; width: 68px; height: 68px; }
  .icon--phone  { left: 128px; top: 397px; width: 64px; height: 48px; }
  .icon--mobile { left: 138px; top: 478px; width: 44px; height: 70px; }
  .icon--mail   { left: 130px; top: 594px; width: 60px; height: 34px; }
</style>
</head>
<body>
  <main class="card">
    <div class="card__pattern" role="img" aria-label="Soft black and white zebra stripe background pattern"></div>

    <header class="card__header">
      <h1 class="card__name">Marisa Dunn</h1>
      <p class="card__title">Proprietor</p>
    </header>
    <div class="card__rule"></div>

    <svg class="icon icon--home" viewBox="0 0 68 68" aria-hidden="true">
      <path d="M4 32 L34 5 L64 32"/>
      <path d="M12 25 V62 H56 V25"/>
      <rect x="18" y="38" width="9" height="10"/>
      <rect x="32" y="40" width="9" height="22"/>
      <rect x="45" y="36" width="8" height="10"/>
    </svg>
    <p class="contact contact--address">12, Rosemont Ave<br>Sunvale, CA 91734</p>

    <svg class="icon icon--phone" viewBox="0 0 64 48" aria-hidden="true">
      <path d="M4 16 C4 6 60 6 60 16 L58 21 L46 19 L46 13 C38 10 26 10 18 13 L18 19 L6 21 Z"/>
      <path d="M18 19 L10 44 H54 L46 19"/>
      <circle cx="32" cy="32" r="7"/>
    </svg>
    <p class="contact contact--phone">246813579</p>

    <svg class="icon icon--mobile" viewBox="0 0 44 70" aria-hidden="true">
      <rect x="3" y="2" width="38" height="66" rx="5"/>
      <rect x="8" y="10" width="28" height="40"/>
      <circle cx="22" cy="59" r="3.5"/>
      <line x1="10" y1="59" x2="15" y2="59"/>
      <line x1="29" y1="59" x2="34" y2="59"/>
    </svg>
    <p class="contact contact--mobile">975318642</p>

    <svg class="icon icon--mail" viewBox="0 0 60 34" aria-hidden="true">
      <rect x="2" y="2" width="56" height="30"/>
      <path d="M2 2 L30 20 L58 2"/>
      <path d="M2 32 L24 16 M58 32 L36 16"/>
    </svg>
    <p class="contact contact--email">velvettebymd@velvettebymd.com</p>
  </main>
</body>
</html>
```